MRT Property - Business Cards

Looking for a business card & general letterhead, signage etc design for our new logo.

Colours:
000a20
0056a2
00b5ef
0088ce
68cef2

Fonts:
Poppins
Karla

Please keep look and feel of new brand - example in the zip package I sent.

```html
<!DOCTYPE html>
<html lang="en">
<head>
<meta charset="utf-8">
<title>MRT Property – Business Cards</title>
<link href="https://fonts.googleapis.com/css2?family=Poppins:wght@300;400;700&family=Karla:wght@400;500&display=swap" rel="stylesheet">
<style>
  :root {
    --ink: #000a20;
    --brand-blue: #0056a2;
    --sky: #00b5ef;
    --mid-blue: #0088ce;
    --pale-blue: #68cef2;
    --paper: #ffffff;
    --backdrop: #1f2026;
  }
  html, body {
    margin: 0;
    padding: 0;
    width: 1200px;
    height: 900px;
    overflow: hidden;
    background: var(--backdrop);
  }
  .canvas {
    position: relative;
    width: 1200px;
    height: 900px;
  }
  .card {
    position: absolute;
    left: 320px;
    width: 560px;
    height: 320px;
    border-radius: 18px;
    box-sizing: border-box;
    overflow: hidden;
  }
  .card--front {
    top: 100px;
    background: var(--brand-blue);
    display: flex;
    align-items: center;
    justify-content: center;
    gap: 18px;
  }
  .brand-dot {
    width: 54px;
    height: 54px;
    border-radius: 50%;
    background: var(--pale-blue);
    flex: none;
  }
  .card--back {
    top: 480px;
    background: var(--paper);
    padding: 34px 40px;
  }
  .brand-panel {
    position: absolute;
    top: 0;
    right: 0;
    width: 250px;
    height: 100%;
    background: linear-gradient(160deg, var(--sky) 0%, var(--mid-blue) 45%, var(--pale-blue) 100%);
  }
  .card__content {
    position: relative;
    width: 260px;
  }
  .wordmark {
    font-family: "Poppins", sans-serif;
    font-weight: 700;
    letter-spacing: 0.5px;
    margin: 0;
    white-space: nowrap;
  }
  .card--front .wordmark {
    color: var(--paper);
    font-size: 50px;
  }
  .card--back .wordmark {
    color: var(--brand-blue);
    font-size: 32px;
    line-height: 1;
  }
  .person {
    margin-top: 30px;
  }
  .person__name {
    font-family: "Poppins", sans-serif;
    font-weight: 300;
    font-size: 28px;
    color: var(--brand-blue);
    margin: 0;
    line-height: 1.1;
  }
  .person__role {
    font-family: "Karla", sans-serif;
    font-weight: 500;
    font-size: 15px;
    color: var(--ink);
    margin: 2px 0 0;
  }
  .address {
    font-family: "Karla", sans-serif;
    font-style: normal;
    font-size: 14px;
    line-height: 1.35;
    color: var(--ink);
    margin-top: 14px;
  }
  .contact-list {
    list-style: none;
    margin: 14px 0 0;
    padding: 0;
    font-family: "Karla", sans-serif;
    font-size: 14px;
    color: var(--ink);
  }
  .contact-list li {
    display: flex;
    align-items: center;
    gap: 10px;
    line-height: 1.6;
  }
  .contact-list svg {
    width: 13px;
    height: 13px;
    flex: none;
  }
</style>
</head>
<body>
<main class="canvas">
  <section class="card card--front" aria-label="Business card front">
    <span class="brand-dot" aria-hidden="true"></span>
    <h1 class="wordmark">MRT Property</h1>
  </section>

  <section class="card card--back" aria-label="Business card back">
    <div class="brand-panel" role="img" aria-label="Large brand graphic in layered blues"></div>
    <div class="card__content">
      <p class="wordmark">MRT Property</p>
      <div class="person">
        <p class="person__name">Dana Reyes</p>
        <p class="person__role">Managing Director</p>
      </div>
      <address class="address">48 Cedar Ridge Lane<br>Brandon, MS 39042</address>
      <ul class="contact-list">
        <li>
          <svg viewBox="0 0 16 16" aria-hidden="true"><path d="M3.5 1.5l2.5 0 1 3.5-1.7 1.2a8 8 0 0 0 4.5 4.5L11 9l3.5 1v2.5c0 1-1 2-2 2C6.5 14.5 1.5 9.5 1.5 3.5c0-1 1-2 2-2z" fill="var(--mid-blue)"/></svg>
          555.214.7730
        </li>
        <li>
          <svg viewBox="0 0 16 16" aria-hidden="true"><rect x="1" y="3" width="14" height="10" rx="1.5" fill="var(--mid-blue)"/><path d="M1.5 4l6.5 5 6.5-5" fill="none" stroke="var(--paper)" stroke-width="1.3"/></svg>
          info@mrtproperty.com
        </li>
        <li>
          <svg viewBox="0 0 16 16" aria-hidden="true"><circle cx="8" cy="8" r="6.5" fill="var(--mid-blue)"/><path d="M1.5 8h13M8 1.5c-2.5 3-2.5 10 0 13M8 1.5c2.5 3 2.5 10 0 13" fill="none" stroke="var(--paper)" stroke-width="1"/></svg>
          www.mrtproperty.com
        </li>
      </ul>
    </div>
  </section>
</main>
</body>
</html>
```